Letterhead Creation

I would like to create a letterhead incorporating my family crest attached. My current letterhead with my information is also attached. I would also like to add my Paralegal Rosalind Pembry

```html
<!DOCTYPE html>
<html lang="en">
<head>
<meta charset="utf-8">
<title>Letterhead – Law Offices of Martin J. Holloway</title>
<link rel="stylesheet" href="https://fonts.googleapis.com/css2?family=Arimo:wght@400;700&display=swap">
<style>
  :root {
    --navy: #2b2a80;
    --crest-tint: #b3b4dc;
    --paper: #ffffff;
    --ink: #111111;
    --backdrop: #ecebe8;
  }
  * { margin: 0; padding: 0; box-sizing: border-box; }
  html, body { width: 1200px; height: 800px; overflow: hidden; }
  body {
    background: var(--backdrop);
    font-family: "Arimo", Arial, sans-serif;
    color: var(--ink);
    position: relative;
  }
  .sheet {
    position: absolute;
    left: 305px; top: 20px;
    width: 590px; height: 760px;
    background: var(--paper);
    box-shadow: 0 4px 18px rgba(0,0,0,.15);
    overflow: hidden;
  }
  .masthead {
    height: 128px;
    background: var(--navy);
    color: #fff;
    position: relative;
  }
  .crest-box {
    position: absolute; left: 26px; top: 22px;
    width: 86px; height: 86px;
    background: #fff;
    border-radius: 6px;
    padding: 6px;
  }
  .crest-box .crest-fill {
    width: 100%; height: 100%;
    border-radius: 3px;
    background: radial-gradient(circle at 50% 55%, #4a4aa0 0%, #8f90c8 60%, #dcdcef 100%);
  }
  .firm-name {
    position: absolute; left: 170px; top: 22px;
    font-size: 19px; font-weight: 700; letter-spacing: .5px;
  }
  .firm-address {
    position: absolute; left: 172px; top: 50px;
    font-size: 10.5px;
  }
  .firm-paralegal {
    position: absolute; left: 172px; top: 66px;
    font-size: 10.5px;
  }
  .firm-contacts {
    position: absolute; left: 140px; top: 92px;
    display: flex; gap: 18px;
    font-size: 11px;
  }
  .firm-contacts span { display: inline-flex; align-items: center; gap: 5px; }
  .firm-contacts svg { width: 12px; height: 12px; }
  .crest-watermark {
    position: absolute; left: 175px; top: 205px;
    width: 290px; height: 330px;
    background: radial-gradient(ellipse at 50% 55%, var(--crest-tint) 0%, rgba(179,180,220,.55) 55%, rgba(179,180,220,0) 78%);
  }
  .letter {
    position: absolute; left: 30px; top: 152px; right: 16px;
    font-size: 10px; font-weight: 700; line-height: 1.25;
  }
  .letter p { margin-bottom: 13px; }
  .letter .body-text { line-height: 1.6; white-space: nowrap; }
  .letter .signoff { margin-top: 22px; margin-bottom: 34px; }
  .footer-band {
    position: absolute; left: 0; bottom: 0;
    width: 100%; height: 26px;
    background: var(--navy);
  }
</style>
</head>
<body>
  <main class="sheet">
    <header class="masthead">
      <div class="crest-box"><div class="crest-fill" role="img" aria-label="Family crest"></div></div>
      <h1 class="firm-name">LAW OFFICES OF MARTIN J. HOLLOWAY</h1>
      <p class="firm-address">Martin Holloway Esq. 412 N. Alder Ave. Linwood, Ca 91700</p>
      <p class="firm-paralegal">Paralegal: Rosalind Pembry</p>
      <div class="firm-contacts">
        <span><svg viewBox="0 0 12 12"><rect x="2.5" y="0.5" width="7" height="11" rx="1.2" fill="none" stroke="#fff" stroke-width="1.2"/></svg>(555) 201-4417</span>
        <span><svg viewBox="0 0 12 12"><rect x="0.5" y="0.5" width="11" height="11" rx="2" fill="#fff"/><path d="M3 7.5h6v2H3zM3.5 4.5c1.5-1.5 3.5-1.5 5 0" fill="none" stroke="#2b2a80" stroke-width="1.2"/></svg>(555) 318-0922</span>
        <span><svg viewBox="0 0 12 12"><rect x="0.5" y="0.5" width="11" height="11" rx="2" fill="#fff"/><path d="M2.5 4l3.5 2.5L9.5 4" fill="none" stroke="#2b2a80" stroke-width="1.2"/></svg>martin@hollowaylawpc.com</span>
      </div>
    </header>

    <div class="crest-watermark" role="img" aria-label="Faint family crest watermark"></div>

    <section class="letter">
      <p>Northfield Services<br>Daniel Prescott<br>P: 555-410-2236<br>P.O. Box 000000<br>Ridgeway, CO 80000<br>northfieldservices.com</p>
      <p>August 28, 2011</p>
      <p>First Last Name<br>Street Address<br>City, State 00000</p>
      <p>Dear :</p>
      <p class="body-text">Lorem ipsum dolor sit amet, consectetur adipiscing elit. Aenean ut ipsum eget massa fringilla<br>
      Aliquam porta lectus nec mauris ornare venenatis. Vivamus non est turpis, et cursus lorem.<br>
      Morbi imperdiet neque vehicula nunc convallis gravida. Vestibulum iaculis pretium placerat.<br>
      Morbi imperdiet neque vehicula nunc convallis gravida. Vestibulum iaculis pretium placerat<br>
      Etiam pellentesque, velit id dapibus fermentum, turpis sapien ornare dui, ac tincidunt ligula</p>
      <p class="signoff">Sincerely,</p>
      <p>Daniel Prescott<br>NorthfieldServices.com<br>P.O. Box 000000<br>Ridgeway, CO 80000<br>P: (555) 410-2236</p>
    </section>

    <div class="footer-band"></div>
  </main>
</body>
</html>
```